Brellwick Partners, LLC Stationary

Brellwick Partners, LLC is a new financial planning and consulting company. We are looking for designs on business cards, letterhead, envelopes, and anything else that would be useful. Our preference for business card design is two sided. We are looking for a professional and clean look with incorporating the logo and patriotic feel. Thank you to all who participate and good luck!

```html
<!DOCTYPE html>
<html lang="en">
<head>
<meta charset="UTF-8">
<title>Brellwick Partners, LLC — Business Card</title>
<link rel="stylesheet" href="https://fonts.googleapis.com/css2?family=Arimo:wght@400;700&family=Montserrat:wght@600&display=swap">
<style>
  :root {
    --navy: #173d6b;
    --navy-deep: #123259;
    --red: #c8202e;
    --white: #ffffff;
    --paper-shade: #e4e5e7;
    --backdrop: #ecebea;
    --ink-grey: #5a5f66;
  }
  * { margin: 0; padding: 0; box-sizing: border-box; }
  html, body {
    width: 1200px;
    height: 950px;
    overflow: hidden;
    background: var(--backdrop);
    font-family: "Arimo", Arial, sans-serif;
  }
  .sheet {
    position: relative;
    width: 1200px;
    height: 950px;
  }
  .card {
    position: absolute;
    left: 250px;
    width: 700px;
    height: 400px;
    overflow: hidden;
    box-shadow: 0 8px 24px rgba(0,0,0,0.18);
  }
  /* Back side */
  .card-back {
    top: 50px;
    background: linear-gradient(120deg, var(--white) 0%, #f6f6f7 55%, var(--paper-shade) 100%);
  }
  .back-mark {
    position: absolute;
    top: 150px;
    left: 0;
    width: 100%;
    display: flex;
    align-items: center;
    justify-content: center;
    gap: 16px;
  }
  .back-mark .mark-dot {
    width: 26px; height: 26px;
    border-radius: 50%;
    background: var(--red);
  }
  .back-mark .brand-name {
    font-family: "Montserrat", Arial, sans-serif;
    font-weight: 600;
    font-size: 40px;
    letter-spacing: 1px;
    color: var(--navy);
  }
  .back-web {
    position: absolute;
    top: 262px;
    width: 100%;
    text-align: center;
    font-size: 20px;
    letter-spacing: 2px;
    color: var(--ink-grey);
  }
  /* Front side */
  .card-front {
    top: 500px;
    background: linear-gradient(120deg, var(--white) 40%, #f3f3f4 75%, var(--paper-shade) 100%);
  }
  .front-band {
    position: absolute;
    inset: 0;
    width: 700px;
    height: 400px;
  }
  .band-fill { fill: var(--navy); }
  .band-rule { fill: none; stroke: var(--red); stroke-width: 6; }
  .holder {
    position: absolute;
    top: 34px;
    left: 34px;
    color: var(--white);
  }
  .holder-name {
    font-weight: 700;
    font-size: 26px;
    letter-spacing: 0.5px;
    text-transform: uppercase;
  }
  .holder-title {
    font-size: 18px;
    text-transform: uppercase;
    margin-top: 2px;
  }
  .contact {
    position: absolute;
    top: 150px;
    left: 34px;
    color: var(--white);
    font-size: 18px;
    line-height: 25px;
    list-style: none;
  }
  .contact li { display: flex; align-items: center; gap: 9px; }
  .contact .address-line { padding-left: 0; }
  .contact svg { width: 16px; height: 16px; fill: var(--white); flex: none; }
  .front-mark {
    position: absolute;
    top: 176px;
    left: 360px;
    display: flex;
    align-items: center;
    gap: 12px;
  }
  .front-mark .mark-dot {
    width: 20px; height: 20px;
    border-radius: 50%;
    background: var(--red);
  }
  .front-mark .brand-name {
    font-family: "Montserrat", Arial, sans-serif;
    font-weight: 600;
    font-size: 27px;
    letter-spacing: 0.5px;
    color: var(--navy);
  }
</style>
</head>
<body>
<main class="sheet">

  <section class="card card-back" aria-label="Business card, back side">
    <div class="back-mark">
      <span class="mark-dot"></span>
      <span class="brand-name">Brellwick Partners, LLC</span>
    </div>
    <p class="back-web">www.brellwick.com</p>
  </section>

  <section class="card card-front" aria-label="Business card, front side">
    <svg class="front-band" viewBox="0 0 700 400" aria-hidden="true">
      <path class="band-fill" d="M0,0 H330 Q250,180 300,400 H0 Z"/>
      <path class="band-rule" d="M342,0 Q262,180 312,400"/>
    </svg>

    <div class="holder">
      <p class="holder-name">Daniel Hartley</p>
      <p class="holder-title">President</p>
    </div>

    <ul class="contact">
      <li class="address-line">2170 Linden Crest Road</li>
      <li class="address-line">Ashford Hills, NY 11920</li>
      <li>
        <svg viewBox="0 0 16 16"><path d="M3.5 1.5l2.6 2.8-1.4 2a8 8 0 0 0 5 5l2-1.4 2.8 2.6-1.6 2C7.5 14.8 1.2 8.5 1.5 3.1z"/></svg>
        555 0148 2290
      </li>
      <li>
        <svg viewBox="0 0 16 16"><path d="M4 1h8v4H4zM1 6h14v6h-3v3H4v-3H1zM5 10v4h6v-4z"/></svg>
        555 0163 7714
      </li>
      <li>
        <svg viewBox="0 0 16 16"><path d="M1 3h14v10H1zM2.2 4.2v.4L8 8.6l5.8-4V4.2z"/></svg>
        daniel@brellwick.com
      </li>
      <li>
        <svg viewBox="0 0 16 16"><circle cx="8" cy="8" r="7"/></svg>
        www.brellwick.com
      </li>
    </ul>

    <div class="front-mark">
      <span class="mark-dot"></span>
      <span class="brand-name">Brellwick Partners, LLC</span>
    </div>
  </section>

</main>
</body>
</html>
```